Harborview Estates Business Card for Apartment Buildings

Create business cards for resident managers who run apartment buildings. The audience is the public who are searching for apartment rentals, and current residents who live at the apartment building. Key design element will be incorporating the company logo, however, the logo cannot dominate. The building name and manager name are more important than the logo. Current business card design leaves little room for copy, so we may need to reduce the size on the current card to allow for more space for copy.

Target Market(s)

Adults 18-65 years of age, who are looking for an apartment rental, plus current residents who live at our apartment buildings.

Industry/Entity Type

Property Management

Contact Information for Business Card

A major design element will be use of the company logo. Important property and manager contact information must be part of the design. The size of the logo will need to be reduced to make room for building and manager contact copy.

Font styles to use
Sans Serif

Colors
3176b5
000000
959595
ffffff

Requirements
Must have
• 1) Incorporate the company logo.
• 2) Use the company colors (dark blue, black/grey, over white).
• 3) FEATURE THE BUILDING NAME
• 4) FEATURE THE MANAGER NAME
• 5) The company name is less important than BUILDING and MANAGER
• 6) Manager contact information
• **SEE ATTACHED CREATIVE BRIEF**
Nice to have
• 1) Back of card logo watermark
• 2) Ability to write notes on back of carfd
Should not have
• Avoid letting the company logo dominate the card, the building name and manager are more important than the company logo.

```html
<!DOCTYPE html>
<html lang="en">
<head>
<meta charset="utf-8">
<title>Harborview Estates – Business Card</title>
<link href="https://fonts.googleapis.com/css2?family=Oswald:wght@600&family=Work+Sans:wght@400;600&display=swap" rel="stylesheet">
<style>
  :root {
    --brand-blue: #1f6db3;
    --ink: #2f2f31;
    --muted: #555557;
    --card-dark: #48484a;
    --card-light: #ffffff;
    --backdrop: #e6e6e8;
  }
  html, body {
    margin: 0;
    width: 1200px;
    height: 930px;
    overflow: hidden;
    background: var(--backdrop);
    font-family: "Work Sans", Arial, sans-serif;
  }
  .card {
    position: absolute;
    width: 560px;
    height: 320px;
    border-radius: 16px;
    overflow: hidden;
    box-shadow: 0 10px 24px rgba(0,0,0,0.18);
  }
  /* Back of card */
  .card-back {
    left: 60px;
    top: 110px;
    background: var(--card-dark);
    color: #fff;
  }
  .card-back .watermark-area {
    position: absolute;
    inset: 0;
    background: var(--card-dark);
  }
  .card-back .brand {
    position: absolute;
    left: 0; right: 0;
    top: 120px;
    display: flex;
    align-items: center;
    justify-content: center;
    gap: 14px;
  }
  .brand-dot {
    width: 22px; height: 22px;
    border-radius: 50%;
    flex: none;
  }
  .card-back .brand-dot { background: #fff; }
  .card-back .brand-name {
    font-weight: 600;
    font-size: 34px;
    letter-spacing: 1px;
    color: #fff;
    text-transform: uppercase;
  }
  .card-back .web {
    position: absolute;
    left: 0; right: 0;
    top: 238px;
    text-align: center;
    font-size: 15px;
    letter-spacing: 0.5px;
  }
  /* Front of card */
  .card-front {
    left: 580px;
    top: 500px;
    background: var(--card-light);
    color: var(--ink);
  }
  .card-front .brand {
    position: absolute;
    left: 34px;
    top: 60px;
    display: flex;
    align-items: center;
    gap: 9px;
  }
  .card-front .brand-dot { background: var(--brand-blue); width: 15px; height: 15px; }
  .card-front .brand-name {
    font-weight: 600;
    font-size: 16px;
    color: var(--brand-blue);
    text-transform: uppercase;
    letter-spacing: 0.5px;
    line-height: 1;
  }
  .manager {
    position: absolute;
    right: 36px;
    top: 38px;
    text-align: right;
  }
  .manager-name {
    font-family: "Oswald", "Arial Narrow", sans-serif;
    font-weight: 600;
    font-size: 30px;
    color: var(--brand-blue);
    text-transform: uppercase;
    letter-spacing: -0.5px;
    line-height: 1.05;
  }
  .manager-title {
    font-size: 14px;
    color: var(--muted);
    margin-top: 2px;
  }
  .divider {
    position: absolute;
    left: 40px;
    right: 36px;
    top: 104px;
    height: 1.5px;
    background: var(--brand-blue);
  }
  .address {
    position: absolute;
    right: 36px;
    top: 114px;
    text-align: right;
    font-size: 14px;
    line-height: 19px;
    color: var(--ink);
  }
  .contacts {
    position: absolute;
    left: 40px;
    top: 168px;
    margin: 0;
    padding: 0;
    list-style: none;
    font-size: 14px;
    line-height: 20px;
  }
  .contacts li { display: flex; align-items: center; gap: 10px; }
  .contacts svg { width: 11px; height: 11px; flex: none; }
  .contacts .accent { color: var(--brand-blue); }
  .wave {
    position: absolute;
    left: 0; bottom: 0;
    width: 560px; height: 320px;
  }
</style>
</head>
<body>

<section class="card card-back" aria-label="Back of business card">
  <div class="watermark-area" role="img" aria-label="Faint repeating company mark watermark across the dark card"></div>
  <div class="brand">
    <span class="brand-dot"></span>
    <span class="brand-name">Harborview Estates</span>
  </div>
  <div class="web">www.harborviewest.com</div>
</section>

<section class="card card-front" aria-label="Front of business card">
  <svg class="wave" viewBox="0 0 560 320" aria-hidden="true">
    <path d="M0,308 C250,308 420,272 560,222 L560,320 L0,320 Z" fill="#48484a"/>
    <path d="M0,303 C250,302 420,264 560,212" fill="none" stroke="#1f6db3" stroke-width="4"/>
  </svg>

  <div class="brand">
    <span class="brand-dot"></span>
    <span class="brand-name">Harborview Estates</span>
  </div>

  <div class="manager">
    <div class="manager-name">Marisol Delgado</div>
    <div class="manager-title">Resident Manager</div>
  </div>

  <div class="divider"></div>

  <div class="address">
    Cedar Court Apartments<br>
    2480 Linden Avenue<br>
    Lakeview, CA 90210
  </div>

  <ul class="contacts">
    <li>
      <svg viewBox="0 0 12 12"><path d="M2.5 1 L4.5 1 L5.2 3.6 L4 4.5 C4.6 6 6 7.4 7.5 8 L8.4 6.8 L11 7.5 L11 9.5 C11 10.3 10.3 11 9.5 11 C5 11 1 7 1 2.5 C1 1.7 1.7 1 2.5 1 Z" fill="#1f6db3"/></svg>
      555-201-4480
    </li>
    <li>
      <svg viewBox="0 0 12 12"><rect x="3" y="0.8" width="6" height="10.4" rx="1.2" fill="none" stroke="#1f6db3" stroke-width="1.4"/><circle cx="6" cy="9.2" r="0.7" fill="#1f6db3"/></svg>
      555-318-6027
    </li>
    <li>
      <svg viewBox="0 0 12 12"><rect x="1" y="5" width="10" height="6" rx="1" fill="#1f6db3"/><rect x="3" y="1" width="6" height="4" fill="none" stroke="#1f6db3" stroke-width="1.2"/></svg>
      555-462-9135
    </li>
    <li>
      <svg viewBox="0 0 12 12"><rect x="0.8" y="2.3" width="10.4" height="7.4" fill="none" stroke="#1f6db3" stroke-width="1.3"/><path d="M1 2.6 L6 6.6 L11 2.6" fill="none" stroke="#1f6db3" stroke-width="1.3"/></svg>
      marisol@harborviewest.com
    </li>
    <li>
      <svg viewBox="0 0 12 12"><circle cx="6" cy="6" r="5" fill="none" stroke="#1f6db3" stroke-width="1.2"/><ellipse cx="6" cy="6" rx="2.2" ry="5" fill="none" stroke="#1f6db3" stroke-width="1"/><path d="M1 6 H11" stroke="#1f6db3" stroke-width="1"/></svg>
      <span>www.<span class="accent">harborviewest</span>.com</span>
    </li>
  </ul>
</section>

</body>
</html>
```